A fantastic website for a physio

We are looking for an eye catching website which can attract as many customer as possible.
We have logo designed and ready to be used in the website.
Please use the green and blue which is used in our logo for the preferred colors.
The following are the designs that I Iike:
http://www.example-clinicone.com.au/
http://www.example-rehabtwo.com.au/
We will be having other services including massage therapy, Psychology and podiatrist. You can find information about podiatry in our condition sheet.
for the address you can put Shop 5/248 Wattlebrook Street, Kelvindale. It might change but for now you can leave it until I confirm that in the next couple of days.

Logo file can be downloaded here:
https://files.example-share.net/s/qz4mtl9wkr82bvx/Logo1511.jpg?dl=0

Target Market(s)

Infant to old people.
We speak Farsi.

Industry/Entity Type

Physical Therapy

Number of Pages Required

5+ page

Font styles to use
Serif

Colors
33a6d7
abd037
e667a6

Requirements
Must have
• Home, About , our services, Conditions we treat and contact
• For home page and contacts we would like a tab that can connect to another website(bookwell) for online booking. We would like the patient's to be able to leave us massage or leave their email for monthly news letter. For the condition we treat you can use the condition sheets I have attached. For about us and home page you can use brochure I have attached.
• The other things should have include: in-line contact form, Google Map, clinic hours, newsletter sign-up etc, schema rich contact information
• Social media connection to our Facebook, Instagram and linked in
Nice to have
• Search engine optimization for Merrylands and Parramatta physiotherapy.
• We can speak English and Farsi. So is nice to have an information tab for Farsi speaking people. I can provide you with the texts.

```html
<!DOCTYPE html>
<html lang="en">
<head>
<meta charset="utf-8">
<title>Aligned Motion Physio</title>
<link href="https://fonts.googleapis.com/css2?family=Open+Sans:wght@400;600;700&display=swap" rel="stylesheet">
<style>
:root{
  --blue:#2f9fd6;
  --green:#a3c93a;
  --pink:#e667a6;
  --ink:#333;
  --muted:#666;
  --line:#d9d9d9;
  --paper:#fff;
  --soft:#f4f4f4;
}
*{box-sizing:border-box;margin:0;padding:0}
html,body{width:1200px;height:3523px;overflow:hidden}
body{font-family:"Open Sans",Arial,sans-serif;color:var(--ink);background:var(--paper);position:relative}

/* header */
.site-header{position:absolute;top:0;left:0;width:1200px;height:122px;background:var(--paper);box-shadow:0 2px 4px rgba(0,0,0,.06);z-index:2}
.brand{position:absolute;left:100px;top:24px;display:flex;align-items:center;gap:14px}
.brand-dot{width:60px;height:60px;border-radius:50%;background:var(--green);flex:none}
.brand-name{font-size:29px;font-weight:700;color:var(--blue);line-height:1.05;width:240px}
.contact-chip{position:absolute;top:20px;display:flex;align-items:center;gap:10px;font-size:13px;color:var(--ink)}
.contact-chip .ico{width:34px;height:34px;border-radius:50%;background:var(--pink);display:flex;align-items:center;justify-content:center}
.contact-chip b{font-weight:600}
.contact-chip span.val{color:var(--pink)}
.main-nav{position:absolute;top:86px;left:486px;display:flex;gap:40px;font-size:14px}
.main-nav a{color:var(--ink);text-decoration:none;position:relative}
.main-nav a.active:after{content:"";position:absolute;left:0;right:0;bottom:-17px;height:3px;background:var(--green)}

/* hero */
.hero{position:absolute;top:122px;left:0;width:1200px;height:540px;
  background:
    radial-gradient(ellipse 260px 200px at 640px 120px,rgba(160,155,150,.75),transparent 70%),
    radial-gradient(ellipse 300px 150px at 820px 330px,rgba(210,170,140,.85),transparent 70%),
    radial-gradient(ellipse 200px 90px at 560px 270px,rgba(220,110,140,.55),transparent 70%),
    radial-gradient(ellipse 360px 120px at 760px 470px,rgba(250,250,248,.9),transparent 70%),
    radial-gradient(ellipse 160px 300px at 1120px 260px,rgba(200,175,140,.6),transparent 70%),
    linear-gradient(110deg,#ece9e4 0%,#ddd6cd 45%,#cfc4b6 65%,#efece8 100%)}
.hero-dots{position:absolute;bottom:18px;left:570px;display:flex;gap:8px}
.hero-dots i{width:8px;height:8px;border-radius:50%;background:rgba(255,255,255,.8)}
.appointment{position:absolute;top:165px;left:66px;width:340px;height:443px;background:var(--paper);box-shadow:0 0 12px rgba(0,0,0,.18);padding:24px 28px}
.appointment h2{text-align:center;color:var(--green);font-size:24px;font-weight:700;line-height:1}
.appointment h3{text-align:center;color:var(--blue);font-size:33px;font-weight:700;line-height:1.2;margin-bottom:20px}
.field{border:1px solid var(--line);height:36px;font-size:12px;color:#999;padding:10px 12px;margin-bottom:12px;background:#fff}
.field-row{display:flex;gap:12px}
.field-row .field{flex:1;display:flex;justify-content:space-between}
.field.area{height:62px}
.btn{display:block;background:var(--green);color:#fff;font-weight:700;font-size:15px;text-align:center;text-transform:uppercase}
.appointment .btn{height:44px;line-height:44px;margin-top:4px}

/* booking bands */
.booking{position:absolute;top:662px;width:600px;height:98px;color:#fff;padding:20px 60px}
.booking.phone{left:0;background:var(--blue)}
.booking.online{left:600px;background:var(--green)}
.booking h4{font-size:22px;font-weight:700}
.booking p{font-size:15px;margin-top:2px}
.booking .outline-btn{position:absolute;right:32px;top:30px;border:2px solid #fff;width:124px;height:40px;line-height:36px;text-align:center;font-size:12px;font-weight:700}

/* welcome */
.section-title{position:absolute;left:0;width:1200px;text-align:center;color:var(--blue);font-size:29px;font-weight:700}
.welcome-text{position:absolute;top:878px;left:100px;width:1000px;text-align:center;font-size:13px;line-height:2.1;color:var(--ink)}
.services{position:absolute;top:1012px;left:100px;width:1000px;display:flex;justify-content:space-between}
.service{width:200px;text-align:center}
.service .photo{width:188px;height:188px;margin:0 auto;border-radius:50%;border:7px solid #d3e49a}
.service h5{margin-top:20px;font-size:14px;font-weight:600}
.service p{margin-top:10px;font-size:11.5px;line-height:1.8;color:var(--muted)}
.arrow{position:absolute;top:1085px}

/* feature panels */
.feature{position:absolute;top:1380px;width:600px;height:425px;padding:112px 80px 0;color:#fff}
.feature.move{left:0;background:
  radial-gradient(ellipse 150px 220px at 470px 200px,rgba(120,90,75,.7),transparent 70%),
  radial-gradient(ellipse 140px 200px at 300px 240px,rgba(225,220,210,.45),transparent 70%),
  radial-gradient(ellipse 120px 220px at 60px 300px,rgba(50,80,130,.7),transparent 70%),
  linear-gradient(135deg,#5d6670,#3e4a57 55%,#6c6f73)}
.feature.life{left:600px;background:
  radial-gradient(ellipse 220px 90px at 280px 250px,rgba(255,210,120,.8),transparent 70%),
  radial-gradient(ellipse 300px 120px at 300px 420px,rgba(40,20,5,.8),transparent 70%),
  linear-gradient(180deg,#6e4420,#c9843a 55%,#4a2810)}
.feature h3{font-size:30px;font-weight:700}
.feature p{margin-top:12px;font-size:13px;line-height:1.9}
.feature .btn{width:166px;height:40px;line-height:40px;font-size:13px;margin-top:24px}

/* posts */
.posts{position:absolute;top:1945px;left:100px;width:1000px;display:flex;justify-content:space-between}
.post{width:310px}
.post .photo{height:205px}
.post h5{margin-top:26px;font-size:13.5px;font-weight:700;line-height:1.7}
.post p{margin-top:18px;font-size:12px;line-height:1.8;color:var(--muted)}

/* quick contact */
.quick-form{position:absolute;top:2452px;left:132px;width:400px}
.quick-form .field{height:40px;margin-bottom:14px}
.quick-form .field.area{height:72px}
.quick-form .btn{width:132px;height:42px;line-height:42px;font-size:14px;margin-top:20px}
.map{position:absolute;top:2450px;left:600px;width:468px;height:302px;
  background:radial-gradient(ellipse 200px 140px at 230px 150px,#ececec,transparent 80%),linear-gradient(135deg,#dfdfdf,#e9e9e9 50%,#dcdcdc)}
.map .pin{position:absolute;left:214px;top:118px}
.map .pin-label{position:absolute;left:242px;top:134px;font-size:11px;font-weight:700;color:#c0392b}

/* testimonial */
.testimonial{position:absolute;top:2835px;left:0;width:1200px;height:375px;background:
  radial-gradient(ellipse 260px 260px at 960px 160px,rgba(225,195,170,.75),transparent 70%),
  radial-gradient(ellipse 240px 240px at 260px 220px,rgba(150,175,195,.7),transparent 70%),
  linear-gradient(90deg,#6b7d8c,#93a2ad 45%,#b6c0c6 70%,#7b8b97)}
.testimonial .shade{position:absolute;inset:0;background:rgba(28,70,110,.4)}
.quote-mark{position:absolute;top:62px;left:580px;font-size:64px;font-weight:700;color:#fff;line-height:1}
.testimonial blockquote{position:absolute;top:128px;left:180px;width:840px;text-align:center;color:#fff;font-size:12.5px;font-style:italic;line-height:2.3}
.author{position:absolute;top:212px;left:494px;display:flex;align-items:center;gap:18px;color:#fff}
.avatar{width:70px;height:70px;border-radius:50%;border:4px solid #fff;background:#c9c1b8}
.author b{font-size:14px;display:block}
.author span{font-size:12px;color:#e7e7e7}
.t-dots{position:absolute;bottom:22px;left:588px;display:flex;gap:6px}
.t-dots i{width:6px;height:6px;border-radius:50%;background:rgba(255,255,255,.6)}

/* footer */
.site-footer{position:absolute;top:3210px;left:0;width:1200px;height:270px;background:var(--paper)}
.col{position:absolute;top:44px}
.col h6{color:var(--blue);font-size:14px;font-weight:700;margin-bottom:16px}
.col p,.col li{font-size:12px;line-height:1.9;color:var(--muted);list-style:none}
.newsletter .field{width:284px;height:34px;margin:14px 0 16px}
.newsletter .btn{width:108px;height:36px;line-height:36px;font-size:12px}
.info-line{display:flex;align-items:center;gap:8px}
.socials{display:flex;gap:10px;margin:14px 0 16px}
.socials i{width:34px;height:34px;border-radius:50%;display:block}
.foot-brand{display:flex;align-items:center;gap:10px}
.foot-brand .brand-dot{width:40px;height:40px}
.foot-brand .brand-name{font-size:17px;width:150px}
.copyright{position:absolute;top:3480px;left:0;width:1200px;height:43px;background:#ececec;text-align:center;font-size:12px;line-height:43px;color:var(--muted)}
</style>
</head>
<body>

<header class="site-header">
  <div class="brand"><span class="brand-dot"></span><span class="brand-name">Aligned Motion Physio</span></div>
  <div class="contact-chip" style="left:628px">
    <span class="ico"><svg width="16" height="16" viewBox="0 0 24 24"><path fill="#fff" d="M6.6 10.8a15 15 0 0 0 6.6 6.6l2.2-2.2c.3-.3.7-.4 1-.2 1.1.4 2.3.6 3.6.6.6 0 1 .4 1 1V20c0 .6-.4 1-1 1A17 17 0 0 1 3 4c0-.6.4-1 1-1h3.5c.6 0 1 .4 1 1 0 1.3.2 2.5.6 3.6.1.3 0 .7-.2 1z"/></svg></span>
    <span><b>Call Us :</b> <span class="val">+61.400123456</span></span>
  </div>
  <div class="contact-chip" style="left:842px">
    <span class="ico"><svg width="16" height="16" viewBox="0 0 24 24"><rect x="3" y="5" width="18" height="14" rx="2" fill="#fff"/><path d="M3 6l9 7 9-7" stroke="#e667a6" stroke-width="2" fill="none"/></svg></span>
    <span><b>Email Us :</b> <span class="val">hello@alignedmotion.example</span></span>
  </div>
  <nav class="main-nav">
    <a class="active">Home</a><a>About us</a><a>Services</a><a>Conditions we treat</a><a>Contact</a><a>English &#9662;</a>
  </nav>
</header>

<section class="hero" role="img" aria-label="Physiotherapist treating a patient's shoulder on a treatment table">
  <div class="hero-dots"><i></i><i></i><i></i><i></i></div>
</section>

<form class="appointment">
  <h2>MAKE AN</h2>
  <h3>APPOINTMENT</h3>
  <div class="field">Name</div>
  <div class="field">Email</div>
  <div class="field">Phone</div>
  <div class="field-row"><div class="field">Date <span>&#9633;</span></div><div class="field">Time <span>&#9675;</span></div></div>
  <div class="field area">Comments</div>
  <span class="btn">Submit Now!</span>
</form>

<div class="booking phone"><h4>Phone Booking</h4><p>Lorem Ipsum is simply dummy text of the printing</p><span class="outline-btn">CLICK HERE</span></div>
<div class="booking online"><h4>Online Booking</h4><p>Lorem Ipsum is simply dummy text of the printing</p><span class="outline-btn">CLICK HERE</span></div>

<h2 class="section-title" style="top:818px">Welcome to Aligned Motion Physio</h2>
<p class="welcome-text">We are an outpatient rehabilitation center staffed with physical therapists, massage therapists, and an athletic trainer.<br>We believe that during rehabilitation, the patient should be educated by their therapist in order to be able to maintain maximum flexibility and<br>pain-free living long after our work ends.</p>

<svg class="arrow" style="left:62px" width="16" height="44" viewBox="0 0 16 44"><path d="M14 2L2 22l12 20" stroke="#ccc" stroke-width="2" fill="none"/></svg>
<svg class="arrow" style="left:1122px" width="16" height="44" viewBox="0 0 16 44"><path d="M2 2l12 20L2 42" stroke="#ccc" stroke-width="2" fill="none"/></svg>

<div class="services">
  <div class="service"><div class="photo" role="img" aria-label="Massage therapy on a knee" style="background:radial-gradient(circle at 40% 35%,#f0d4bd,#c99878 55%,#8e6a58)"></div><h5>Massage therapy</h5><p>Achilles tendinopathy is an unfortunately common complaint seen in a physiotherapy clinic.</p></div>
  <div class="service"><div class="photo" role="img" aria-label="Neck and upper back pain" style="background:radial-gradient(circle at 50% 40%,#e8452f 0,#d98a70 22%,#b9836c 55%,#6e4a3a)"></div><h5>Podiatrist</h5><p>It is a fact that approximately 8 out of every 10 people will experience at least some form...</p></div>
  <div class="service"><div class="photo" role="img" aria-label="Spine model in a clinic" style="background:radial-gradient(circle at 45% 45%,#fbf8f2,#ddd2c0 50%,#9db4c8)"></div><h5>Psychology</h5><p>Commonly called "herniated disc" or "ruptured disc" (or misleadingly called "slipped disc...</p></div>
  <div class="service"><div class="photo" role="img" aria-label="Person with a headache" style="background:radial-gradient(circle at 50% 45%,#e8cdb8,#b58e78 55%,#5e4638)"></div><h5>Headaches</h5><p>If you suffer from persistent or recurring headaches, it may be that they are coming...</p></div>
</div>

<section class="feature move" role="img" aria-label="Therapist explaining movement with a skeleton model">
  <h3>Maximizing Movement</h3>
  <p>We help you learn to work with your body to restore mobility through concentrated, specialized exercises and stretches. Our patients typically find their movement is restored without needing surgery.</p>
  <span class="btn">Read More Info</span>
</section>
<section class="feature life" role="img" aria-label="Runners at sunset">
  <h3>Quality of Life Improvement</h3>
  <p>Chronic pain and movement limitation mean that you enjoy your life less. We find what is wrong and we also find out what you want to be able to do physically. We help you heal your body so you can live your fullest life.</p>
  <span class="btn">Read More Info</span>
</section>

<h2 class="section-title" style="top:1862px">Recent Posts</h2>
<div class="posts">
  <article class="post"><div class="photo" role="img" aria-label="Woman exercising with a resistance band" style="background:radial-gradient(ellipse 90px 80px at 200px 80px,rgba(220,120,80,.5),transparent 70%),linear-gradient(135deg,#f3f1ee,#c9d8d0 60%,#3f9fa0)"></div><h5>Lorem Ipsum is simply dummy text of the printing and typesetting</h5><p>Lorem Ipsum is simply dummy text of the printing and typesetting industry. Lorem Ipsum has been the industry's standard dummy text ever...</p></article>
  <article class="post"><div class="photo" role="img" aria-label="Group stretching in a fitness class" style="background:radial-gradient(ellipse 160px 70px at 150px 90px,rgba(215,160,130,.8),transparent 70%),linear-gradient(135deg,#e4e0dc,#a69d95 60%,#3f3a36)"></div><h5>Lorem Ipsum is simply dummy text of the printing and typesetting</h5><p>Lorem Ipsum is simply dummy text of the printing and typesetting industry. Lorem Ipsum has been the industry's standard dummy text ever...</p></article>
  <article class="post"><div class="photo" role="img" aria-label="People training on gym equipment" style="background:radial-gradient(ellipse 60px 90px at 90px 90px,rgba(230,90,150,.7),transparent 70%),linear-gradient(135deg,#5a6f8e,#2d3b55 60%,#8aa0b8)"></div><h5>Lorem Ipsum is simply dummy text of the printing and typesetting</h5><p>Lorem Ipsum is simply dummy text of the printing and typesetting industry. Lorem Ipsum has been the industry's standard dummy text ever...</p></article>
</div>

<h2 class="section-title" style="top:2362px">Quick Contact</h2>
<form class="quick-form">
  <div class="field">Name</div>
  <div class="field">Email</div>
  <div class="field">Phone</div>
  <div class="field area">Message</div>
  <span class="btn">Submit Now</span>
</form>
<div class="map" role="img" aria-label="Street map showing the clinic location">
  <svg class="pin" width="24" height="34" viewBox="0 0 24 34"><path d="M12 0C5.4 0 0 5.2 0 11.7 0 20 12 34 12 34s12-14 12-22.3C24 5.2 18.6 0 12 0z" fill="#d9342b"/><circle cx="12" cy="11.5" r="4.5" fill="#fff"/></svg>
  <span class="pin-label">12 Fernlea Street</span>
</div>

<section class="testimonial" role="img" aria-label="Women exercising in a fitness class">
  <div class="shade"></div>
  <div class="quote-mark">&#8220;</div>
  <blockquote>Lorem Ipsum is simply dummy text of the printing and typesetting industry. Lorem Ipsum has been the industry's standard dummy text ever since the 1500s, when an unknown printer took a galley of type and scrambled it to make a type specimen book.</blockquote>
  <div class="author"><span class="avatar"></span><div><b>MARCUS HALE</b><span>- Business man -</span></div></div>
  <div class="t-dots"><i></i><i></i><i></i></div>
</section>

<footer class="site-footer">
  <div class="col newsletter" style="left:100px">
    <h6>Newsletter signup</h6>
    <p>Get our recent updates through your email id</p>
    <div class="field">Enter your email id</div>
    <span class="btn">Subscribe</span>
  </div>
  <div class="col" style="left:438px">
    <h6>Aligned Motion Physio</h6>
    <p>12 Fernlea Street, Kelvindale,<br>New South Wales, Australia</p>
    <p class="info-line"><svg width="12" height="12" viewBox="0 0 24 24"><path fill="#a3c93a" d="M6.6 10.8a15 15 0 0 0 6.6 6.6l2.2-2.2c.3-.3.7-.4 1-.2 1.1.4 2.3.6 3.6.6.6 0 1 .4 1 1V20c0 .6-.4 1-1 1A17 17 0 0 1 3 4c0-.6.4-1 1-1h3.5c.6 0 1 .4 1 1 0 1.3.2 2.5.6 3.6.1.3 0 .7-.2 1z"/></svg>+61.400123456</p>
    <p class="info-line"><svg width="12" height="12" viewBox="0 0 24 24"><rect x="2" y="5" width="20" height="14" rx="2" fill="#a3c93a"/></svg>hello@alignedmotion.example</p>
    <p class="info-line"><svg width="12" height="12" viewBox="0 0 24 24"><circle cx="12" cy="12" r="10" fill="#a3c93a"/><path d="M12 6v6l4 2" stroke="#fff" stroke-width="2" fill="none"/></svg>Mon - Sat : 9.00am to 8.00pm</p>
    <p style="padding-left:20px">Sunday : 9.00 am to 2.00pm</p>
  </div>
  <div class="col" style="left:715px">
    <h6>Welcome</h6>
    <ul><li>Home</li><li>About us</li><li>Services</li><li>Blog</li><li>Testimonials</li><li>Contact us</li></ul>
  </div>
  <div class="col" style="left:870px">
    <h6>Social media</h6>
    <p>Connect with our social network</p>
    <div class="socials"><i style="background:#3b64a8"></i><i style="background:#3fb2e4"></i><i style="background:#d9362f"></i><i style="background:#2f7bb5"></i></div>
    <div class="foot-brand"><span class="brand-dot"></span><span class="brand-name">Aligned Motion Physio</span></div>
  </div>
</footer>
<div class="copyright">Copyright &copy; Aligned Motion Physio, 2016 All rights reserved.</div>

</body>
</html>
```